Social Media Graphics - Oakline Push REVISED

Create 6-7 individual social media graphics (square size) to encourage folks to join our online course called:

The Harvest Ledger Circle
How to Launch a Multi-Million Business From Scratch
Sign Up Today!

IMPORTANT: Make the largest and most prominent text on the graphic be: How to Launch a Multi-Million Business From Scratch

For the color scheme of the graphics, let's try a blue color palette; make sure the graphics appeal to both men and women

Make sure each graphic contains 1 of the 3 pics attached (crop pic as needed); and make sure one of the graphics is all TEXT only.

Target Market(s)

men and women looking to start a business

Industry/Entity Type

Entrepreneurship

Colors
0054AA
0677BA
7BADD7
CADEEF
E8F1F8

Requirements
Must have
• All the text and use the 3 pics provided; one graphic can be all text; Simple, modern design that's easy to read

```html
<!DOCTYPE html>
<html lang="en">
<head>
<meta charset="utf-8">
<title>The Harvest Ledger Circle – Social Graphics</title>
<link href="https://fonts.googleapis.com/css2?family=Poppins:wght@400;500;600;700;800&display=swap" rel="stylesheet">
<style>
  :root{
    --blue-deep:#0054AA;
    --blue-mid:#0677BA;
    --blue-soft:#7BADD7;
    --blue-pale:#CADEEF;
    --blue-mist:#E8F1F8;
    --ink:#1f2a3a;
    --white:#ffffff;
    --canvas:#f6f6f6;
  }
  *{box-sizing:border-box;margin:0;padding:0}
  html,body{width:1200px;height:830px;overflow:hidden;background:var(--canvas);font-family:'Poppins',sans-serif}
  .board{position:relative;width:1200px;height:830px}
  .tile{position:absolute;width:600px;height:600px;overflow:hidden;transform:scale(.5733);transform-origin:0 0;box-shadow:0 4px 14px rgba(0,0,0,.18)}
  .tile svg.bg{position:absolute;inset:0;width:600px;height:600px}
  .photo{position:absolute}
  .title{position:absolute;font-weight:600;line-height:1.15;letter-spacing:.2px}
  .headline{position:absolute;font-weight:800;line-height:1.18;letter-spacing:.1px}
  .btn{position:absolute;display:flex;align-items:center;justify-content:center;background:var(--white);color:#111;border-radius:10px;font-weight:500;box-shadow:0 3px 8px rgba(0,0,0,.25)}
  .outline{-webkit-text-stroke:1.2px var(--blue-deep);color:var(--white)}
  .outline--light{-webkit-text-stroke:1.2px var(--white);color:var(--blue-deep)}
  .center{left:0;right:0;text-align:center}

  .t1{left:42px;top:45px;background:#0f6fb0}
  .t2{left:428px;top:45px;background:linear-gradient(135deg,#1262c2 0%,#2f86d2 55%,#6fb6e6 100%)}
  .t3{left:814px;top:45px;background:var(--white)}
  .t4{left:42px;top:442px;background:var(--blue-deep)}
  .t5{left:428px;top:442px;background:var(--blue-deep)}
  .t6{left:814px;top:442px;background:var(--blue-deep)}
</style>
</head>
<body>
<main class="board">

  <!-- Graphic 1: angled photo with pale panel -->
  <section class="tile t1">
    <svg class="bg" viewBox="0 0 600 600" aria-hidden="true">
      <polygon points="349,102 600,102 600,467 226,467" fill="var(--blue-pale)"/>
      <polygon points="0,494 232,494 222,525 0,525" fill="var(--blue-soft)"/>
    </svg>
    <svg class="photo" style="left:0;top:0" width="600" height="600" viewBox="0 0 600 600" role="img" aria-label="Photo of the two course hosts smiling, arms crossed">
      <defs><linearGradient id="p1" x1="0" y1="0" x2="1" y2="1"><stop offset="0" stop-color="#6a4a3e"/><stop offset=".5" stop-color="#2a2f3e"/><stop offset="1" stop-color="#1d3f6e"/></linearGradient></defs>
      <polygon points="0,75 358,75 217,494 0,494" fill="url(#p1)"/>
    </svg>
    <h2 class="title" style="left:358px;top:122px;width:225px;font-size:24px;color:var(--blue-mid)">The Harvest<br>Ledger Circle</h2>
    <p class="headline" style="left:358px;top:190px;width:230px;font-size:28px;color:var(--blue-deep)">How to Launch a Multi-Million Business From Scratch</p>
    <div class="btn" style="left:355px;top:390px;width:176px;height:40px;border:3px solid var(--blue-mid);border-radius:20px;font-size:14px">Sign Up Today!</div>
  </section>

  <!-- Graphic 2: photo over blue gradient, centred type -->
  <section class="tile t2">
    <div class="photo" role="img" aria-label="Cut-out photo of the two course hosts smiling" style="left:55px;top:20px;width:505px;height:375px;border-radius:46% 40% 30% 34%;background:linear-gradient(160deg,#6b4c40,#23273a 55%,#1b4a86)"></div>
    <h2 class="title center" style="top:408px;font-size:26px;color:var(--white)">The Harvest Ledger Circle</h2>
    <p class="headline center" style="top:448px;font-size:30px;color:var(--white)">How to Launch a Multi-Million<br>Business From Scratch</p>
    <div class="btn" style="left:218px;top:546px;width:165px;height:38px;font-size:15px">Sign Up Today!</div>
  </section>

  <!-- Graphic 3: arc and circular portrait -->
  <section class="tile t3">
    <svg class="bg" viewBox="0 0 600 600" aria-hidden="true">
      <path d="M120,225 A180,180 0 0 1 478,225" fill="none" stroke="var(--blue-deep)" stroke-width="44" stroke-linecap="round"/>
      <rect x="0" y="475" width="600" height="125" fill="var(--blue-deep)"/>
      <rect x="38" y="398" width="524" height="170" fill="var(--white)"/>
      <circle cx="598" cy="100" r="28" fill="var(--blue-deep)"/>
      <circle cx="572" cy="148" r="12" fill="var(--blue-mid)"/>
      <circle cx="551" cy="118" r="7" fill="var(--blue-pale)"/>
      <circle cx="26" cy="273" r="13" fill="var(--blue-deep)"/>
      <circle cx="48" cy="304" r="7" fill="var(--blue-pale)"/>
      <circle cx="0" cy="320" r="30" fill="var(--blue-deep)"/>
    </svg>
    <div class="photo" role="img" aria-label="Circular photo of the two course hosts standing together" style="left:160px;top:88px;width:276px;height:276px;border-radius:50%;border:6px solid var(--blue-mid);background:linear-gradient(135deg,#f2b8c2,#c8305a 45%,#25262e)"></div>
    <h2 class="title center" style="top:402px;font-size:26px;color:var(--blue-deep)">The Harvest Ledger <span class="outline">Circle</span></h2>
    <p class="headline center" style="top:440px;font-size:27px;color:var(--blue-deep)">How to Launch a Multi-Million<br>Business From Scratch</p>
    <div class="btn" style="left:223px;top:522px;width:154px;height:30px;font-size:14px">Sign Up Today!</div>
  </section>

  <!-- Graphic 4: framed, split blue with inset photo -->
  <section class="tile t4">
    <svg class="bg" viewBox="0 0 600 600" aria-hidden="true">
      <rect x="364" y="0" width="236" height="600" fill="#4d8ccf"/>
      <rect x="15" y="15" width="570" height="570" fill="none" stroke="var(--white)" stroke-width="9"/>
      <circle cx="85" cy="279" r="30" fill="none" stroke="var(--blue-soft)" stroke-width="3"/>
      <g fill="var(--white)">
        <rect x="505" y="495" width="7" height="7"/><rect x="532" y="495" width="7" height="7"/><rect x="559" y="495" width="7" height="7"/>
        <rect x="451" y="518" width="7" height="7"/><rect x="478" y="518" width="7" height="7"/><rect x="505" y="518" width="7" height="7"/><rect x="532" y="518" width="7" height="7"/><rect x="559" y="518" width="7" height="7"/>
        <rect x="424" y="541" width="7" height="7"/><rect x="451" y="541" width="7" height="7"/><rect x="478" y="541" width="7" height="7"/><rect x="505" y="541" width="7" height="7"/><rect x="532" y="541" width="7" height="7"/><rect x="559" y="541" width="7" height="7"/>
      </g>
    </svg>
    <h2 class="title" style="left:44px;top:42px;font-size:26px;color:var(--white)">The Harvest Ledger Circle</h2>
    <p class="headline" style="left:44px;top:84px;width:510px;font-size:32px;color:var(--white)">How to Launch a Multi-Million Business From Scratch</p>
    <div class="btn" style="left:44px;top:190px;width:155px;height:36px;font-size:15px">Sign Up Today!</div>
    <div class="photo" role="img" aria-label="Photo of the two hosts speaking on stage" style="left:92px;top:273px;width:402px;height:236px;border:5px solid var(--white);background:linear-gradient(120deg,#d9d6d0,#8b8d96 45%,#2d3650)"></div>
  </section>

  <!-- Graphic 5: full photo with angled blue footer -->
  <section class="tile t5">
    <div class="photo" role="img" aria-label="Photo of the two hosts presenting with a microphone" style="left:0;top:0;width:600px;height:420px;background:linear-gradient(180deg,#e8e4de,#b9b4ad 55%,#4a4a52)"></div>
    <svg class="bg" viewBox="0 0 600 600" aria-hidden="true">
      <polygon points="250,392 600,338 600,520" fill="var(--blue-soft)"/>
      <polygon points="0,308 250,392 600,520 600,600 0,600" fill="var(--blue-deep)"/>
      <rect x="18" y="10" width="564" height="578" fill="none" stroke="var(--white)" stroke-width="3"/>
    </svg>
    <h2 class="title" style="left:34px;top:444px;font-size:23px;color:var(--white)">The Harvest Ledger Circle</h2>
    <p class="headline" style="left:34px;top:478px;font-size:27px;color:var(--white)">How to Launch a Multi-Million<br>Business From Scratch</p>
    <div class="btn" style="left:365px;top:548px;width:200px;height:32px;font-size:13px;background:var(--blue-deep);color:var(--white);border:2px solid var(--white);border-radius:16px">Sign Up Today!&nbsp;›</div>
  </section>

  <!-- Graphic 6: text only -->
  <section class="tile t6">
    <svg class="bg" viewBox="0 0 600 600" aria-hidden="true">
      <path d="M0,0 L290,0 C320,60 300,120 200,150 C120,175 80,200 0,215 Z" fill="#9db7d7"/>
      <path d="M0,430 C80,450 150,470 190,540 C210,575 200,600 200,600 L0,600 Z" fill="#9db7d7"/>
      <path d="M380,600 C420,520 520,490 600,500 L600,600 Z" fill="#9db7d7"/>
      <path d="M290,0 C360,60 470,90 600,100" fill="none" stroke="var(--blue-pale)" stroke-width="5"/>
      <path d="M0,380 C120,470 220,600 330,590 C430,580 520,540 600,545" fill="none" stroke="var(--blue-pale)" stroke-width="5"/>
      <g fill="var(--white)">
        <rect x="525" y="0" width="7" height="7"/><rect x="550" y="0" width="7" height="7"/><rect x="575" y="0" width="7" height="7"/>
        <rect x="525" y="30" width="7" height="7"/><rect x="550" y="30" width="7" height="7"/><rect x="575" y="30" width="7" height="7"/>
        <rect x="525" y="59" width="7" height="7"/><rect x="550" y="59" width="7" height="7"/><rect x="575" y="59" width="7" height="7"/>
        <rect x="525" y="88" width="7" height="7"/><rect x="550" y="88" width="7" height="7"/><rect x="575" y="88" width="7" height="7"/>
        <rect x="525" y="117" width="7" height="7"/><rect x="550" y="117" width="7" height="7"/><rect x="575" y="117" width="7" height="7"/>
        <rect x="525" y="146" width="7" height="7"/><rect x="550" y="146" width="7" height="7"/><rect x="575" y="146" width="7" height="7"/>
      </g>
    </svg>
    <h2 class="title center" style="top:226px;font-size:28px;color:var(--white)">The Harvest Ledger <span class="outline outline--light">Circle</span></h2>
    <p class="headline center" style="top:272px;font-size:32px;color:var(--white)">How to Launch a Multi-Million<br>Business From Scratch</p>
    <div class="btn" style="left:200px;top:382px;width:200px;height:44px;font-size:18px">Sign Up Today!</div>
  </section>

</main>
</body>
</html>
```